Debt Collection Website Design! We are the solution for landlords to get paid what they are owed.

We are a 3rd party debt collection company that specializes in Residential and Commercial real estate debt collection. We help landlords recover money from past residents by being fair, friendly and aggressive. We also collect/buy/sell/trade civil judgments won resulting from anything from automobile accidents to evictions to a pet zebra getting stolen. We buy single judgments to large portfolios, we also collect judgments for a nominal fee.

I would like a new, modern, easy to navigate website. A spot that we can post news stories or updated information about our company. I have included our company logo that must be on the top of the page. Feel free to ask any questions that will help get the process going.

Target Market(s)

Landlords, small to large apartment complex. Real estate services and lawyers.

Industry/Entity Type

Real Estate

Number of Pages Required

3 page

Requirements
Must have
• Company logo which has been attached. A page where we can explain the collection process, fees and placement. A page where we can explain judgments, collection vs. selling, placement form. I am open to any font/designs and willing to work with anyone.
Nice to have
• Nice to have a spot on the homepage to place news articles about ourselves and our industry.
Should not have
• I don't want it over crowded. Simple, sleek and easy to navigate is best. No gavels on any of the pages. It cannot look legal, say/show anything that we use legal powers to collect. We are not a law office, we don't practice law, we are 3rd party debt collection agency.

```html
<!DOCTYPE html>
<html lang="en">
<head>
<meta charset="utf-8">
<title>Halvorsen Recovery, LLC</title>
<link rel="stylesheet" href="https://fonts.googleapis.com/css2?family=Crimson+Pro:wght@400;500&family=Open+Sans:wght@400;600&display=swap">
<style>
:root{
  --navy:#0e2a74;
  --navy-deep:#0a2266;
  --slate:#4a5663;
  --text:#555b63;
  --muted:#7d838a;
  --line:#d9dcdf;
  --footer:#222325;
  --footer-text:#a9adb2;
  --white:#ffffff;
}
*{margin:0;padding:0;box-sizing:border-box}
html,body{width:1176px;height:1200px;overflow:hidden;background:var(--white)}
body{position:relative;font-family:"Open Sans",Arial,sans-serif;color:var(--text)}
.abs{position:absolute}
.serif{font-family:"Crimson Pro",Georgia,serif}

/* header */
.brand{left:97px;top:17px;display:flex;align-items:center;gap:12px}
.brand-square{width:60px;height:56px;background:var(--navy)}
.brand-name{font-family:"Crimson Pro",Georgia,serif;font-size:36px;font-weight:400;color:var(--navy);line-height:1;letter-spacing:.5px}
.phone{right:98px;top:22px;display:flex;align-items:center;gap:7px;font-size:19px;color:var(--navy)}
.nav{right:98px;top:66px;display:flex;gap:30px;font-size:12px;letter-spacing:.2px}
.nav a{color:#7a8088;text-decoration:none}
.nav a.active{color:var(--navy)}

/* hero */
.hero{left:0;top:106px;width:1176px;height:403px;overflow:hidden}
.hero-photo{position:absolute;inset:0;background:linear-gradient(90deg,#5a4a44 0%,#8d7f78 18%,#c9c6c3 45%,#e9e9ea 70%,#f2f2f2 100%)}
.hero-panel{position:absolute;inset:0}
.hero-copy{left:827px;top:121px;width:260px;font-size:25px;line-height:31px;color:var(--white)}
.btn-outline-light{left:827px;top:345px;width:86px;height:30px;border:1px solid var(--white);color:var(--white);font-size:10.5px;display:flex;align-items:center;justify-content:center}
.slide-arrow{top:292px;width:29px;height:29px;background:rgba(40,50,60,.55);display:flex;align-items:center;justify-content:center}

/* main */
.h2{font-family:"Crimson Pro",Georgia,serif;font-size:24px;color:var(--navy);font-weight:400}
.intro{left:97px;top:580px;width:690px;font-size:11px;line-height:18.5px}
.btn-outline{width:78px;height:30px;border:1px solid #6b7077;color:#444;font-size:10.5px;display:flex;align-items:center;justify-content:center}
.divider{left:97px;top:727px;width:688px;height:1px;background:var(--line)}
.service{top:796px;width:216px}
.service-photo{width:216px;height:133px}
.service-title{margin-top:18px;font-size:13.5px;line-height:18.5px;color:var(--navy)}
.service-text{margin-top:8px;font-size:9.5px;line-height:15px;color:var(--muted)}
.more{position:absolute;top:264px;left:2px;font-size:10.5px;color:#222;display:flex;align-items:center;gap:3px}

/* sidebar */
.sidebar{left:816px;top:509px;width:360px;height:580px;background:linear-gradient(90deg,#eceeef 0%,#fafafa 25%,#ffffff 60%)}
.news-band{left:816px;top:533px}
.news-band-label{left:842px;top:540px;font-size:20px;color:var(--white)}
.news-item{left:843px;width:228px}
.news-date{width:83px;height:26px;border:1px solid #c9ccd0;background:var(--white);font-size:10px;color:#555;display:flex;align-items:center;justify-content:center}
.news-title{margin-top:14px;font-size:10.8px;line-height:15px;color:var(--navy)}
.news-text{margin-top:7px;font-size:8.7px;line-height:15px;color:var(--muted)}
.news-rule{margin-top:9px;height:1px;background:var(--line)}
.view-all{left:843px;top:1059px;font-size:10px;color:#333;text-decoration:underline}

/* footer */
.footer{left:0;top:1117px;width:1176px;height:83px;background:var(--footer)}
.footer-links{left:97px;top:1135px;font-size:11.5px;color:var(--footer-text);word-spacing:2px}
.footer-links span{margin:0 9px;color:#777}
.copyright{left:97px;top:1165px;font-size:11px;color:var(--footer-text)}
.social{right:98px;top:1145px;display:flex;gap:7px}
.social i{display:block;width:27px;height:27px;border-radius:50%;background:#3c4654}
</style>
</head>
<body>

<header>
  <div class="abs brand">
    <div class="brand-square"></div>
    <div class="brand-name">Halvorsen Recovery, LLC</div>
  </div>
  <div class="abs phone">
    <svg width="14" height="14" viewBox="0 0 24 24"><path fill="#0e2a74" d="M6.6 10.8a15.1 15.1 0 0 0 6.6 6.6l2.2-2.2c.3-.3.7-.4 1-.2 1.1.4 2.3.6 3.6.6.6 0 1 .4 1 1V20c0 .6-.4 1-1 1C10.6 21 3 13.4 3 4c0-.6.4-1 1-1h3.5c.6 0 1 .4 1 1 0 1.3.2 2.5.6 3.6.1.3 0 .7-.2 1l-2.3 2.2z"/></svg>
    <span>555 014 2290</span>
  </div>
  <nav class="abs nav">
    <a class="active">HOME</a><a>ABOUT US</a><a>SERVICES</a><a>CONTACT US</a>
  </nav>
</header>

<section class="abs hero">
  <div class="hero-photo" role="img" aria-label="Photo of a smiling agent in a blue shirt holding a folder in front of a house"></div>
  <svg class="hero-panel" width="1176" height="403" viewBox="0 0 1176 403">
    <defs>
      <radialGradient id="panelGlow" cx="0.75" cy="0.15" r="0.9">
        <stop offset="0" stop-color="#2544a0"/>
        <stop offset="0.5" stop-color="#102c7a"/>
        <stop offset="1" stop-color="#0a2266"/>
      </radialGradient>
    </defs>
    <polygon points="808,0 1176,0 1176,403 808,403 646,201" fill="#ffffff"/>
    <polygon points="815,0 1176,0 1176,403 815,403 654,201" fill="url(#panelGlow)"/>
  </svg>
  <div class="abs slide-arrow" style="left:0">
    <svg width="12" height="12" viewBox="0 0 12 12"><path d="M11 6H2M6 2L2 6l4 4" stroke="#d8dce2" stroke-width="2" fill="none"/></svg>
  </div>
  <div class="abs slide-arrow" style="left:1147px">
    <svg width="12" height="12" viewBox="0 0 12 12"><path d="M1 6h9M6 2l4 4-4 4" stroke="#d8dce2" stroke-width="2" fill="none"/></svg>
  </div>
</section>
<div class="abs hero-copy serif">Aenean sed quam non sapien faucibus conse quat vitae sit...</div>
<div class="abs btn-outline-light">CONTACT US</div>

<aside>
  <div class="abs sidebar"></div>
  <svg class="abs news-band" width="252" height="42" viewBox="0 0 252 42"><polygon points="0,0 226,0 252,21 226,42 0,42" fill="#4a5663"/></svg>
  <div class="abs news-band-label serif">Latest News</div>

  <div class="abs news-item" style="top:597px">
    <div class="news-date">Feb 24, 0215</div>
    <div class="news-title">Maecenas vel tortor accumsan quam varius imperdiet vel eget</div>
    <div class="news-text">Nulla facilisi. Etiam vel massa elementum, bibendum tellus venenatis, feugiat massa. Curabitur venenatis lacinia ornare.</div>
    <div class="news-rule"></div>
  </div>
  <div class="abs news-item" style="top:753px">
    <div class="news-date">Feb 24, 0215</div>
    <div class="news-title">Maecenas vel tortor accumsan quam varius imperdiet vel eget</div>
    <div class="news-text">Nulla facilisi. Etiam vel massa elementum, bibendum tellus venenatis, feugiat massa. Curabitur venenatis lacinia ornare.</div>
    <div class="news-rule"></div>
  </div>
  <div class="abs news-item" style="top:909px">
    <div class="news-date">Feb 24, 0215</div>
    <div class="news-title">Maecenas vel tortor accumsan quam varius imperdiet vel eget</div>
    <div class="news-text">Nulla facilisi. Etiam vel massa elementum, bibendum tellus venenatis, feugiat massa. Curabitur venenatis lacinia ornare.</div>
    <div class="news-rule"></div>
  </div>
  <div class="abs view-all">VIEW ALL</div>
</aside>

<main>
  <h2 class="abs h2" style="left:97px;top:538px">Welcome to Halvorsen Recovery, LLC</h2>
  <p class="abs intro">Pellentesque convallis molestie enim sit amet efficitur. Etiam id imperdiet lectus. Vivamus lacus justo, ultrices nec erat in, euismod iaculis mauris. Vivamus eleifend vitae nulla vel malesuada. In ac malesuada lacus, et consectetur ante. Fusce vitae lectus sit amet mi pulvinar maximus. Aenean placerat, nibh vel accumsan aliquet, magna nibh accumsan nibh, ac tempus nunc ipsum ac tellus. Cras augue magna, placerat eget nulla non, congue suscipit neque.</p>
  <div class="abs btn-outline" style="left:97px;top:670px">READ MORE</div>
  <div class="abs divider"></div>

  <h2 class="abs h2" style="left:97px;top:753px">Our Services</h2>

  <article class="abs service" style="left:98px">
    <div class="service-photo" role="img" aria-label="Photo of two hands passing banknotes" style="background:radial-gradient(circle at 50% 45%,#8a8684,#4a4745 80%)"></div>
    <div class="service-title">Residential and Commercial Real estate Debt Collection.</div>
    <div class="service-text">Proin porta fermentum ipsum, vel porttitor turpis venenatis luctus. Vivamus volutpat eu sapien quis tempus.</div>
    <div class="more">READ MORE <svg width="5" height="8" viewBox="0 0 5 8"><path d="M0 0l5 4-5 4z" fill="#222"/></svg></div>
  </article>

  <article class="abs service" style="left:333px">
    <div class="service-photo" role="img" aria-label="Photo of a landlord talking with a tenant at a doorway" style="background:linear-gradient(90deg,#d9d3c9,#c9b08d 55%,#8aa3c0)"></div>
    <div class="service-title">Landlords Recover Money from Past Residents</div>
    <div class="service-text">Proin porta fermentum ipsum, vel porttitor turpis venenatis luctus. Vivamus volutpat eu sapien quis tempus.</div>
    <div class="more">READ MORE <svg width="5" height="8" viewBox="0 0 5 8"><path d="M0 0l5 4-5 4z" fill="#222"/></svg></div>
  </article>

  <article class="abs service" style="left:568px">
    <div class="service-photo" role="img" aria-label="Photo of a hand holding house keys over a signed document" style="background:linear-gradient(180deg,#4d5e86 0%,#8a7a6a 45%,#b8936a 100%)"></div>
    <div class="service-title">We also Collect/Buy/Sell/Trade Civil Judgments</div>
    <div class="service-text">Proin porta fermentum ipsum, vel porttitor turpis venenatis luctus. Vivamus volutpat eu sapien quis tempus.</div>
    <div class="more">READ MORE <svg width="5" height="8" viewBox="0 0 5 8"><path d="M0 0l5 4-5 4z" fill="#222"/></svg></div>
  </article>
</main>

<footer>
  <div class="abs footer"></div>
  <div class="abs footer-links">Home<span>|</span>About us<span>|</span>Services<span>|</span>Contact us</div>
  <div class="abs copyright">Copyright &copy; 2015 &nbsp;Halvorsen Recovery, LLC. &nbsp;All rights reserved.</div>
  <div class="abs social">
    <i aria-label="Social link"></i><i aria-label="Social link"></i><i aria-label="Social link"></i><i aria-label="Email link"></i>
  </div>
</footer>

</body>
</html>
```